Awesome photographers card for an awesome new business

Double sided business card Black background and silver logo in middle on one side. Details on otherside. please keep it simple

Industry/Entity Type

Photographer

Contact Information for Business Card

Gerald Fenwick
0452817360
GeraldFenwickPhotography47@mailbox.test
www.GeraldFenwickPhotography.test.au
Instagram _Gerald_fenwick

Requirements
Must have
• My logo in Silver
• please use instagram logo instead of "Instagram"

```html
<!DOCTYPE html>
<html lang="en">
<head>
<meta charset="utf-8">
<title>Gerald Fenwick Photography – Business Card</title>
<link href="https://fonts.googleapis.com/css2?family=Open+Sans:wght@400;700&display=swap" rel="stylesheet">
<style>
  :root {
    --stage: #2e2a28;
    --card: #141414;
    --silver: #c8c8c8;
    --silver-dim: #8a8a8a;
    --white: #f2f2f2;
    --rule: #5a5a5a;
  }
  * { margin: 0; padding: 0; box-sizing: border-box; }
  html, body { width: 1200px; height: 864px; overflow: hidden; }
  body {
    background: var(--stage);
    font-family: "Open Sans", sans-serif;
    position: relative;
  }
  .card {
    position: absolute;
    width: 540px;
    height: 310px;
    background: var(--card);
    border-radius: 4px;
    box-shadow: 0 12px 30px rgba(0,0,0,.45);
  }
  .card--front { left: 70px; top: 90px; }
  .card--back { left: 590px; top: 460px; }

  .brand-mark {
    width: 150px; height: 150px;
    border: 3px solid var(--silver);
    border-radius: 50%;
    display: flex; align-items: center; justify-content: center;
    text-align: center;
    color: var(--silver);
    font-weight: 700;
    font-size: 17px;
    line-height: 1.25;
    letter-spacing: 1px;
    text-transform: uppercase;
  }
  .card--front .brand-mark {
    position: absolute; left: 195px; top: 52px;
  }
  .front-url {
    position: absolute; left: 0; right: 0; top: 240px;
    text-align: center;
    color: var(--silver-dim);
    font-size: 14px;
    letter-spacing: 2px;
  }

  .card--back .brand-mark {
    position: absolute; left: 30px; top: 82px;
    width: 140px; height: 140px; font-size: 16px;
  }
  .divider {
    position: absolute; left: 200px; top: 70px;
    width: 1px; height: 170px;
    background: var(--rule);
  }
  .details { position: absolute; left: 222px; top: 84px; }
  .details__name {
    color: var(--white);
    font-weight: 700;
    font-size: 18px;
    text-transform: uppercase;
    margin-bottom: 14px;
  }
  .contact-list { list-style: none; }
  .contact-list li {
    display: flex; align-items: center; gap: 9px;
    color: var(--white);
    font-size: 13px;
    line-height: 22px;
  }
  .contact-list svg { width: 12px; height: 12px; flex: none; fill: var(--white); }
</style>
</head>
<body>
  <section class="card card--front" aria-label="Card front">
    <div class="brand-mark">Gerald<br>Fenwick</div>
    <p class="front-url">www.GeraldFenwickPhotography.test.au</p>
  </section>

  <section class="card card--back" aria-label="Card back">
    <div class="brand-mark">Gerald<br>Fenwick</div>
    <div class="divider"></div>
    <div class="details">
      <h1 class="details__name">Gerald Fenwick</h1>
      <ul class="contact-list">
        <li>
          <svg viewBox="0 0 12 12" aria-hidden="true"><path d="M2 1h2.5l1 3-1.5 1a7 7 0 0 0 3 3l1-1.5 3 1V11h-1.5A9.5 9.5 0 0 1 1 2.5V1z"/></svg>
          0452817360
        </li>
        <li>
          <svg viewBox="0 0 12 12" aria-hidden="true"><path d="M0 2h12v8H0z M1 3l5 3.5L11 3" fill="none" stroke="#f2f2f2" stroke-width="1.2"/></svg>
          GeraldFenwickPhotography47@mailbox.test
        </li>
        <li>
          <svg viewBox="0 0 12 12" aria-hidden="true"><circle cx="6" cy="6" r="5" fill="none" stroke="#f2f2f2" stroke-width="1.2"/><path d="M1 6h10M6 1c-3 3-3 7 0 10M6 1c3 3 3 7 0 10" fill="none" stroke="#f2f2f2"/></svg>
          www.GeraldFenwickPhotography.test.au
        </li>
        <li>
          <svg viewBox="0 0 12 12" aria-hidden="true"><rect x="0" y="0" width="12" height="12" rx="2"/></svg>
          _Gerald_fenwick
        </li>
      </ul>
    </div>
  </section>
</body>
</html>
```